Business card, Invoice and printable service brochure

I need a 5.5x8.5 invoice, business card and printable service template for reception desk designed for my Rug repair, restoration and cleaning business.

I have included a picture for reference

www.velborenrug.example

Columns i need in my invoice:
Type of rug, Size, Background Color, Repair needs, Notes, Price and rug cleaning disclaimer.

Target Market(s)

Higher segment clients

Industry/Entity Type

Rug Repair, Restoration and cleaning,

Requirements
Must have
• Services hast to be listed on the invoice as well as service brochure.

```html
<!DOCTYPE html>
<html lang="en">
<head>
<meta charset="utf-8">
<title>Velboren Rug – Business Card</title>
<link href="https://fonts.googleapis.com/css2?family=Lato:wght@700&family=Lustria&display=swap" rel="stylesheet">
<style>
  :root {
    --canvas: #e4e4e4;
    --card-dark: #1b1b1b;
    --gold: #c4a672;
    --ink-light: #ffffff;
    --rug-deep: #2a120a;
    --rug-red: #9c3418;
    --rug-ochre: #c48a3a;
  }
  * { margin: 0; padding: 0; box-sizing: border-box; }
  html, body { width: 1200px; height: 1200px; overflow: hidden; }
  body { background: var(--canvas); position: relative; font-family: "Lato", sans-serif; }

  .card { position: absolute; background: var(--card-dark); overflow: hidden; }

  /* Front */
  .card--front { left: 234px; top: 132px; width: 729px; height: 416px; }
  .rug-photo {
    position: absolute; left: 0; top: 0; width: 305px; height: 416px;
    background:
      radial-gradient(ellipse at 30% 40%, var(--rug-ochre) 0%, transparent 55%),
      radial-gradient(ellipse at 75% 65%, var(--rug-red) 0%, transparent 60%),
      linear-gradient(135deg, var(--rug-red), var(--rug-deep) 60%, var(--rug-ochre));
  }
  .front-tab { position: absolute; left: 305px; top: 72px; width: 14px; height: 46px; background: var(--gold); }
  .front-name {
    position: absolute; left: 378px; top: 72px;
    font-family: "Lustria", serif; font-size: 44px; color: var(--gold); letter-spacing: 1px;
  }
  .contact-list { position: absolute; left: 377px; top: 0; list-style: none; }
  .contact-item { position: absolute; left: 0; display: flex; align-items: flex-start; white-space: nowrap; }
  .contact-item svg { width: 31px; height: 31px; flex: none; }
  .contact-text {
    margin-left: 14px; font-weight: 700; font-size: 19px; line-height: 24px;
    color: var(--ink-light); padding-top: 3px;
  }
  .contact-item--mobile { top: 208px; }
  .contact-item--phone { top: 247px; }
  .contact-item--email { top: 286px; }
  .contact-item--address { top: 327px; }

  /* Back */
  .card--back { left: 250px; top: 640px; width: 681px; height: 416px; border-bottom: 1px solid var(--gold); border-right: 1px solid var(--gold); }
  .back-band { position: absolute; left: 0; top: 0; width: 94px; height: 416px; background: var(--gold); }
  .back-tab { position: absolute; left: 94px; top: 70px; width: 14px; height: 47px; background: var(--gold); }
  .brand-name {
    position: absolute; left: 174px; width: 438px; top: 56px; text-align: center;
    font-family: "Lustria", serif; font-size: 62px; line-height: 70px; color: var(--gold); white-space: nowrap;
  }
  .brand-tagline {
    position: absolute; left: 160px; width: 466px; top: 121px; text-align: center;
    font-family: "Lustria", serif; font-size: 13px; letter-spacing: 4.4px; color: var(--gold); white-space: nowrap;
  }
  .web-address {
    position: absolute; left: 94px; right: 0; top: 348px; text-align: center;
    font-weight: 700; font-size: 24px; color: var(--gold);
  }
  .web-address .domain { color: var(--ink-light); }
</style>
</head>
<body>

<section class="card card--front">
  <div class="rug-photo" role="img" aria-label="Close-up photograph of a hand-knotted Persian rug with ochre, red and black floral motifs"></div>
  <div class="front-tab"></div>
  <h1 class="front-name">Velboren Rug</h1>
  <ul class="contact-list">
    <li class="contact-item contact-item--mobile">
      <svg viewBox="0 0 32 32" fill="none" stroke="var(--gold)" stroke-width="2"><circle cx="16" cy="16" r="14.5"/><rect x="11.5" y="8" width="9" height="16" rx="1.5"/><line x1="15" y1="21" x2="17" y2="21"/></svg>
      <span class="contact-text">(555)014-2270</span>
    </li>
    <li class="contact-item contact-item--phone">
      <svg viewBox="0 0 32 32" fill="none" stroke="var(--gold)" stroke-width="2"><circle cx="16" cy="16" r="14.5"/><path d="M11 9c-1.5 1-2 2.5-1.5 4.5 1.2 4.2 4.8 7.8 9 9 2 .5 3.5 0 4.5-1.5l-3-2.5-2 1.3c-2-1-3.8-2.8-4.8-4.8l1.3-2z" stroke-linejoin="round"/></svg>
      <span class="contact-text">(555)014-2270</span>
    </li>
    <li class="contact-item contact-item--email">
      <svg viewBox="0 0 32 32" fill="none" stroke="var(--gold)" stroke-width="2"><circle cx="16" cy="16" r="14.5"/><rect x="8" y="15" width="9" height="5" rx="2.5" transform="rotate(-45 12.5 17.5)"/><rect x="15" y="12" width="9" height="5" rx="2.5" transform="rotate(-45 19.5 14.5)"/></svg>
      <span class="contact-text">info@velborenrug.example</span>
    </li>
    <li class="contact-item contact-item--address">
      <svg viewBox="0 0 32 32" fill="none" stroke="var(--gold)" stroke-width="2"><circle cx="16" cy="16" r="14.5"/><path d="M16 25c-4-5-6-8-6-11a6 6 0 0 1 12 0c0 3-2 6-6 11z"/><circle cx="16" cy="14" r="2"/></svg>
      <span class="contact-text">1820 Marlow Ave,<br>Brookfield, IL 60999</span>
    </li>
  </ul>
</section>

<section class="card card--back">
  <div class="back-band"></div>
  <div class="back-tab"></div>
  <h2 class="brand-name">VELBOREN RUG</h2>
  <p class="brand-tagline">REPAIR | RESTORATION | CLEANING</p>
  <p class="web-address">www.<span class="domain">velborenrug</span>.example</p>
</section>

</body>
</html>
```